Commercial/Corporate Law Firm needs Website Design

Hi guys. I've started up a new law firm and would love your help designing an attractive website. I'll need both design and coding, and to make it easy for us to edit as necessary later, I think it should be built off a Wordpress.org structure.
FIRST IMPRESSIONS
It's very important that the first impression of the website really captures our prospective clients' attention and impresses them. Their first three seconds needs to be good.
I imagine the homepage may be short, with a menu bar and a compelling image, and with a tagline overlaid or underneath (eg. "It's about results.")
The image should be related to our practice areas: eg. IPOs, corporate transactions, or commercial negotiations.
I have previously suggested there could be a skyline image of Sydney or Adelaide. However, because we are based in Adelaide, I don't think Sydney is appropriate - and Adelaide is probably too boring to use.
HOMEPAGE
Being a new firm, we don't have many existing testimonials, and I will be the only lawyer to start with. So we need to focus on the nature of the services we will provide and how my experience can help them. We have an existing logo to use, and I would like the website colour scheme not to clash with that logo (dark blue and white).
After the initial image and tagline there should be a brief introduction to each of the main areas of work, eg. "We specialise in three main areas of practice:"
1. Corporate Transactions and Regulation
2. Business Law and Dispute Resolution
3. Migration Assistance
These should each have an appropriate photo and link to a separate page that briefly describes our services in that area.
Below that there should be a message from me with a photo. Finally, at the bottom, there should be a "Contact Us" section which shows a Google image of our address, contact details, and then our logo with colours inverted.
OTHER PAGES
While we will need some other pages, they should all be fairly simple. I think we will need one page to say "About Us", where I will put information about my experience. I think we will then need one page for each of the 3 areas listed above, which just needs an appropriate image and then text to describe the service. Finally, a "Contact Us" page which I imagine will be the same as the bottom of the homepage.
OTHER DETAILS
For now you can use details from my LinkedIn page to fill out any other text as necessary, or the photo.
Because the logo is square, I would prefer the design of the website also to be rectangular.
Looking forward to seeing your work! Thank you.
Marcus
Potential clients:
Businesses with legal issues or disputes
Companies wishing to list on the stock market

```html
<!DOCTYPE html>
<html lang="en">
<head>
<meta charset="utf-8">
<title>Harwell Legal</title>
<link href="https://fonts.googleapis.com/css2?family=Montserrat:wght@400;500;700;800&display=swap" rel="stylesheet">
<style>
:root{
  --navy:#1e3864;
  --sky-top:#6a89b4;
  --sky-mid:#4d6d9c;
  --city-low:#2c4a78;
  --city-base:#213d6a;
  --grey-card:#e9e9e9;
  --grey-band:#efefef;
  --text:#555;
  --line:#c9c9c9;
  --white:#fff;
}
*{box-sizing:border-box;margin:0;padding:0}
html,body{width:698px;height:1200px;overflow:hidden;background:var(--white)}
body{font-family:'Montserrat',sans-serif;color:var(--text);position:relative}
.abs{position:absolute}

.topbar{left:0;top:0;width:698px;height:27px;background:var(--navy);color:var(--white);font-size:8.5px}
.topbar .contact-item{position:absolute;top:8px;display:flex;align-items:center;gap:6px}
.topbar svg{display:block}

.header{left:0;top:27px;width:698px;height:64px;background:var(--white)}
.brand{position:absolute;left:44px;top:-11px;display:flex;flex-direction:column;align-items:center;width:100px}
.brand-square{width:40px;height:40px;background:var(--navy)}
.brand-name{margin-top:5px;font-size:13px;font-weight:500;letter-spacing:1.5px;color:var(--navy);text-align:center;line-height:15px}
.brand-name .sub{display:block;font-size:8.5px;letter-spacing:5px;line-height:12px;padding-left:5px}
.nav{position:absolute;right:46px;top:29px;display:flex;gap:22px;font-size:9px;letter-spacing:.3px}
.nav a{color:#666;text-decoration:none}
.nav a.active{color:var(--navy)}

.hero{left:0;top:91px;width:698px;height:321px;background:
  linear-gradient(180deg,var(--sky-top) 0%,var(--sky-mid) 35%,var(--city-low) 70%,var(--city-base) 100%)}
.hero-title{left:0;top:205px;width:698px;text-align:center;font-size:30px;font-weight:700;color:var(--white);letter-spacing:.5px;line-height:36px}
.hero-text{left:120px;top:250px;width:458px;text-align:center;font-size:8.6px;line-height:16px;color:var(--white)}

.practice-card{top:387px;width:170px}
.practice-head{height:72px;background:var(--grey-card);text-align:center;position:relative}
.practice-head::before{content:"";position:absolute;left:60px;top:14px;width:50px;height:2px;background:var(--navy)}
.practice-head h3{position:absolute;left:0;right:0;top:29px;font-size:11.4px;font-weight:500;line-height:18px;color:#555}
.practice-photo{height:140px}

.welcome-photo{left:45px;top:636px;width:200px;height:230px;background:linear-gradient(180deg,#fafafa 0%,#eef0f3 30%,#3a3f55 60%,#262a3a 100%)}
.welcome-title{left:303px;top:669px;font-size:24px;font-weight:800;color:var(--navy);letter-spacing:.5px}
.welcome-text{left:303px;top:703px;width:340px;font-size:8.5px;line-height:14.5px;color:var(--text)}
.welcome-text p+p{margin-top:6px}
.btn-read{left:302px;top:791px;width:109px;height:27px;background:var(--navy);color:var(--white);font-size:12px;font-weight:500;display:flex;align-items:center;justify-content:center;border-radius:2px}

.quote-band{left:0;top:866px;width:698px;height:219px;background:var(--grey-band)}
.quote-title{left:0;top:895px;width:698px;text-align:center;font-size:24px;font-weight:800;color:var(--navy);letter-spacing:.3px}
.quote-text{left:119px;top:929px;width:460px;text-align:center;font-size:8.2px;line-height:15px;color:var(--text)}
.field{background:var(--white);border:1px solid var(--line);font-size:8.5px;color:#777;padding:5px 7px}
.btn-send{left:352px;top:1024px;width:169px;height:21px;background:var(--navy);color:var(--white);font-size:11px;font-weight:500;display:flex;align-items:center;justify-content:center;border-radius:2px}

.footer{left:0;top:1085px;width:698px;height:115px;background:var(--navy)}
.footer-brand{left:299px;top:1076px;width:100px;display:flex;flex-direction:column;align-items:center}
.footer-brand .brand-square{background:var(--white)}
.footer-brand .brand-name{color:var(--white)}
.footer-nav{left:0;top:1155px;width:698px;display:flex;justify-content:center;gap:21px;font-size:9px;color:var(--white)}
.footer-copy{left:0;top:1176px;width:698px;text-align:center;font-size:8.5px;color:var(--white)}
</style>
</head>
<body>

<div class="abs topbar">
  <div class="contact-item" style="left:449px">
    <svg width="13" height="9" viewBox="0 0 13 9"><rect width="13" height="9" rx="1" fill="#fff"/><path d="M0.5 0.8 L6.5 5 L12.5 0.8" stroke="#1e3864" stroke-width="1.2" fill="none"/></svg>
    <span>info@harwell-legal.com</span>
  </div>
  <div class="contact-item" style="left:574px">
    <svg width="11" height="11" viewBox="0 0 24 24"><path fill="#fff" d="M6.6 10.8a15.1 15.1 0 0 0 6.6 6.6l2.2-2.2a1 1 0 0 1 1-.25 11.4 11.4 0 0 0 3.6.57 1 1 0 0 1 1 1V20a1 1 0 0 1-1 1A17 17 0 0 1 3 4a1 1 0 0 1 1-1h3.5a1 1 0 0 1 1 1c0 1.25.2 2.45.57 3.57a1 1 0 0 1-.25 1z"/></svg>
    <span>555 014 2290</span>
  </div>
</div>

<header class="abs header">
  <div class="brand">
    <div class="brand-square"></div>
    <div class="brand-name">HARWELL<span class="sub">LEGAL</span></div>
  </div>
  <nav class="nav">
    <a class="active" href="#">HOME</a>
    <a href="#">ABOUT</a>
    <a href="#">PRACTICE AREAS</a>
    <a href="#">CONTACT</a>
  </nav>
</header>

<section class="abs hero" role="img" aria-label="City skyline of high-rise towers under a blue tint"></section>
<h1 class="abs hero-title">IT'S ABOUT RESULT</h1>
<p class="abs hero-text">Lorem Ipsum is simply dummy text of the printing and typesetting industry. Lorem Ipsum has been the industry's standard dummy text ever since the 1500s, when an unknown printer took a galley.</p>

<article class="abs practice-card" style="left:70px">
  <div class="practice-head"><h3>Business Law and<br>Dispute Resolution</h3></div>
  <div class="practice-photo" role="img" aria-label="Silhouetted business people meeting in a bright boardroom" style="background:linear-gradient(180deg,#d9dde4 0%,#8a93a3 55%,#2b2f3a 100%)"></div>
</article>
<article class="abs practice-card" style="left:264px">
  <div class="practice-head"><h3>Migration Assistance</h3></div>
  <div class="practice-photo" role="img" aria-label="Desktop computer and keyboard on a wooden desk" style="background:linear-gradient(160deg,#3a4660 0%,#2b5fa8 40%,#b48a66 75%,#8a6040 100%)"></div>
</article>
<article class="abs practice-card" style="left:458px">
  <div class="practice-head"><h3>Corporate Transactions<br>and Regulation</h3></div>
  <div class="practice-photo" role="img" aria-label="Business handshake over a clipboard" style="background:linear-gradient(160deg,#c9ccd3 0%,#6b7488 45%,#1d2232 100%)"></div>
</article>

<div class="abs welcome-photo" role="img" aria-label="Portrait of the principal lawyer in a dark suit and red tie"></div>
<h2 class="abs welcome-title">WELCOME TO HARWELL</h2>
<div class="abs welcome-text">
  <p>Lorem Ipsum is simply dummy text of the printing and typesetting industry. Lorem Ipsum has been the industry's standard dummy text ever since the 1500s, when an unknown printer took a galley of type and scrambled it to.</p>
  <p>Lorem Ipsum is simply dummy text of the printing and typesetting industry Lorem Ipsum has been the industry's standard dummy text ever since.</p>
</div>
<div class="abs btn-read">READ MORE</div>

<section class="abs quote-band"></section>
<h2 class="abs quote-title">REQUEST A FREE QUOTE</h2>
<p class="abs quote-text">Lorem Ipsum is simply dummy text of the printing and typesetting industry. Lorem Ipsum has been the<br>industry's standard dummy text ever since the 1500s, when an unknown printer took a galley of type.</p>
<div class="abs field" style="left:176px;top:970px;width:170px;height:21px">Name</div>
<div class="abs field" style="left:176px;top:997px;width:170px;height:21px">Email</div>
<div class="abs field" style="left:176px;top:1024px;width:170px;height:21px">Phone</div>
<div class="abs field" style="left:352px;top:970px;width:169px;height:48px">Message</div>
<div class="abs btn-send">SEND</div>

<footer class="abs footer"></footer>
<div class="abs footer-brand">
  <div class="brand-square"></div>
  <div class="brand-name">HARWELL<span class="sub">LEGAL</span></div>
</div>
<div class="abs footer-nav"><span>Home</span><span>About</span><span>Practice areas</span><span>Contact</span></div>
<div class="abs footer-copy">©HARWELL LEGAL– 2018. All Rights Reserved.</div>

</body>
</html>
```